Website Design for Videographer

I am looking to update my website - www.brinolvaske.com. I am a wedding videographer who specialises in natural and documentary videography.

The website will be built by my designer using the Wordpress Plinthworx framework.

Requirements;
I want the website to have a clean white look mixed in with video footage.
Needs to be classy. At the moment my website uses a lot of Gold. On the new look I DO NOT want gold.

Need a web and mobile design for the following 12 pages;

* Home page (need to have example videos and text)
* About (this is about me and my service)
* Videos (examples of my work)
* Testimonials
* Packages
* Contact
* Content (this is to show social media content that I am making in a vertical format and advertise this service).
* Blog (index page for blog)
* Blog pages (individual pages for blog content)
* Wedding Venues Index Page (https://brinolvaske.com/north-east-wedding-venues/)
* Individual venue pages (https://brinolvaske.com/north-east-wedding-venues/marlow-tendle-lodge-wedding-videos/) - Needs to show videos, photos, text as is on the current page.
* Venue Tours (https://brinolvaske.com/wedding-venue-tours/)

My current logo is attached however on the website I want to go for a black and white style for it.

Example styles I like however must not be copied.
https://joswelbrant.co.uk/about/
https://oakandripple.co.uk/ (if done in white)
https://tumblemothpictures.co.uk/

Target Market(s)

Couples getting married aged 25-35

Industry/Entity Type

Weddings

Number of Pages Required

5+ page

Font styles to use
Sans Serif

Requirements
Must have
• A classy look, black and white, use videos and photos.
Should not have
• Gold colour

```html
<!DOCTYPE html>
<html lang="en">
<head>
<meta charset="utf-8">
<title>Brin Olvaske Wedding Films – Contact</title>
<link href="https://fonts.googleapis.com/css2?family=Cinzel:wght@400&family=Poppins:wght@400;500&display=swap" rel="stylesheet">
<style>
  :root{
    --ink:#000;
    --paper:#fff;
    --mist:#f4f4f4;
    --muted:#8c8c8c;
    --body:#444;
    --border:#9a9a9a;
    --footer:#636162;
    --photo-top:#cfd3d0;
    --photo-mid:#5f7a4a;
    --photo-low:#3f5a2c;
  }
  *{box-sizing:border-box;margin:0;padding:0}
  html,body{width:1200px;height:2685px;overflow:hidden;background:var(--paper)}
  body{position:relative;font-family:'Poppins',sans-serif;color:var(--ink)}
  .abs{position:absolute}

  /* header */
  .site-header{left:0;top:0;width:1200px;height:125px;background:var(--paper)}
  .nav-link{position:absolute;top:54px;font-size:12.5px;letter-spacing:.2px;color:var(--ink);text-decoration:none}
  .brand{position:absolute;left:450px;width:300px;text-align:center;top:56px;font-size:21px;font-weight:500;letter-spacing:6px;color:var(--ink)}
  .btn-enquire{position:absolute;left:998px;top:35px;width:136px;height:45px;background:var(--ink);color:var(--paper);font-size:14px;font-weight:500;display:flex;align-items:center;justify-content:center;border-radius:2px}

  /* hero */
  .hero{left:0;top:125px;width:1200px;height:345px;background:var(--mist)}
  .hero-title{position:absolute;left:0;width:1200px;top:100px;text-align:center;font-family:'Cinzel',serif;font-size:61px;line-height:62px;letter-spacing:2px}
  .btn-book{position:absolute;left:500px;top:247px;width:230px;height:61px;background:var(--ink);color:var(--paper);font-size:17px;font-weight:500;display:flex;align-items:center;justify-content:center;padding-left:24px}
  .hero-photo{left:0;top:470px;width:1200px;height:643px;background:linear-gradient(180deg,var(--photo-top) 0%,#8ea07e 28%,var(--photo-mid) 55%,var(--photo-low) 100%)}

  /* intro */
  .contact-title{left:0;top:1210px;width:1200px;text-align:center;font-family:'Cinzel',serif;font-size:57px;letter-spacing:2px}
  .contact-title .soft{color:var(--muted)}
  .contact-intro{left:240px;top:1307px;width:720px;text-align:center;font-size:14.5px;line-height:28px;color:var(--body)}

  /* form area */
  .form-band{left:0;top:1444px;width:1200px;height:884px;background:var(--mist)}
  .form-card{left:100px;top:1545px;width:721px;height:655px;background:var(--paper)}
  .field-label{position:absolute;left:55px;font-size:13.5px;font-weight:500}
  .field{position:absolute;border:1px solid var(--border);border-radius:3px;font-size:11.5px;color:#8a8a8a;padding:0 18px;display:flex;align-items:center}
  .field.area{align-items:flex-start;padding-top:12px}
  .btn-submit{position:absolute;left:270px;top:527px;width:220px;height:60px;background:var(--ink);color:var(--paper);font-size:17px;font-weight:500;display:flex;align-items:center;justify-content:center}

  .contact-item{position:absolute;left:842px;width:300px;text-align:center}
  .contact-icon{display:block;margin:0 auto 14px;width:86px;height:86px}
  .contact-kicker{font-size:19px;font-weight:500;color:var(--muted);line-height:24px}
  .contact-value{font-size:21px;line-height:30px}

  /* footer */
  .site-footer{left:0;top:2328px;width:1200px;height:357px;background:var(--footer);color:var(--paper)}
  .foot-rule{position:absolute;height:1px;background:#d8d8d8}
  .foot-brand{position:absolute;left:450px;width:300px;top:122px;text-align:center;font-size:21px;font-weight:500;letter-spacing:6px}
  .foot-link{position:absolute;top:222px;font-size:12.5px}
  .foot-enquire{position:absolute;left:528px;top:207px;width:136px;height:52px;border:2px solid var(--paper);display:flex;align-items:center;justify-content:center;font-size:14.5px;font-weight:500}
  .copyright{position:absolute;left:66px;top:311px;font-size:10.5px}
  .social{position:absolute;top:314px;width:38px;height:38px;border-radius:50%;border:2px solid var(--paper)}
  .social.solid{background:var(--paper)}
</style>
</head>
<body>

<header class="abs site-header">
  <a class="nav-link" style="left:68px">HOME</a>
  <a class="nav-link" style="left:142px">ABOUT BRIN</a>
  <a class="nav-link" style="left:264px">WEDDING FILMS</a>
  <a class="nav-link" style="left:397px">BLOG</a>
  <div class="brand">BRIN OLVASKE</div>
  <a class="nav-link" style="left:770px">TESTIMONIALS</a>
  <a class="nav-link" style="left:888px">PACKAGES</a>
  <div class="btn-enquire">ENQUIRE</div>
</header>

<section class="abs hero">
  <h1 class="hero-title">NORTH EAST WEDDING<br>VIDEOGRAPHER</h1>
  <div class="btn-book">BOOK WITH ME</div>
</section>
<div class="abs hero-photo" role="img" aria-label="Bride and groom embracing beside a woodland lake surrounded by ferns and trees"></div>

<h2 class="abs contact-title">CONTACT <span class="soft">ME</span></h2>
<p class="abs contact-intro">If you have any questions or need help, please fill out the form below. We are here to help and answer any questions you might have. We look forward to hearing from you.</p>

<section class="abs form-band"></section>
<form class="abs form-card">
  <label class="field-label" style="top:56px">TELL US YOUR NAME *</label>
  <div class="field" style="left:55px;top:83px;width:292px;height:41px">First Name:</div>
  <div class="field" style="left:373px;top:83px;width:292px;height:41px">Last Name:</div>
  <label class="field-label" style="top:148px">ENTER YOUR EMAIL *</label>
  <div class="field" style="left:55px;top:175px;width:611px;height:41px">Email:</div>
  <label class="field-label" style="top:240px">ENTER PHONE NUMBER</label>
  <div class="field" style="left:55px;top:267px;width:611px;height:41px">Phone:</div>
  <label class="field-label" style="top:332px">MESSAGE *</label>
  <div class="field area" style="left:55px;top:359px;width:611px;height:133px">Write us a message</div>
  <div class="btn-submit">SUBMIT NOW</div>
</form>

<div class="contact-item" style="top:1648px">
  <svg class="contact-icon" viewBox="0 0 86 86" aria-hidden="true">
    <circle cx="43" cy="43" r="43" fill="#000"/>
    <path d="M31 26c2-1 4 0 5 2l3 6c1 2 0 4-1 5l-2 2c2 5 6 9 11 11l2-2c1-1 3-2 5-1l6 3c2 1 3 3 2 5l-2 4c-2 3-6 4-10 2-10-5-17-12-22-22-2-4-1-8 2-10z" fill="#fff"/>
    <path d="M47 24a15 15 0 0 1 15 15M47 31a8 8 0 0 1 8 8" stroke="#fff" stroke-width="3" fill="none" stroke-linecap="round"/>
  </svg>
  <div class="contact-kicker">CALL US</div>
  <div class="contact-value">07700 900 318</div>
</div>

<div class="contact-item" style="top:1852px">
  <svg class="contact-icon" viewBox="0 0 86 86" aria-hidden="true">
    <circle cx="43" cy="43" r="43" fill="#000"/>
    <rect x="22" y="30" width="42" height="28" fill="#fff"/>
    <path d="M22 30l21 16 21-16M22 58l15-14M64 58L49 44" stroke="#000" stroke-width="2.5" fill="none"/>
  </svg>
  <div class="contact-kicker">EMAIL US</div>
  <div class="contact-value">films@brinolvaske.com</div>
</div>

<footer class="abs site-footer">
  <div class="foot-rule" style="left:70px;top:137px;width:378px"></div>
  <div class="foot-rule" style="left:757px;top:137px;width:378px"></div>
  <div class="foot-brand">BRIN OLVASKE</div>
  <a class="foot-link" style="left:190px">HOME</a>
  <a class="foot-link" style="left:263px">ABOUT BRIN</a>
  <a class="foot-link" style="left:386px">WEDDING FILMS</a>
  <div class="foot-enquire">ENQUIRE</div>
  <a class="foot-link" style="left:717px">BLOG</a>
  <a class="foot-link" style="left:784px">TESTIMONIALS</a>
  <a class="foot-link" style="left:903px">PACKAGES</a>
  <div class="foot-rule" style="left:70px;top:290px;width:1065px"></div>
  <p class="copyright">Copyright 2010 - 2024 © Brin Olvaske Wedding Films Limited. All Rights Reserved</p>
  <span class="social solid" style="left:984px" aria-label="Social link"></span>
  <span class="social" style="left:1042px" aria-label="Social link"></span>
  <span class="social" style="left:1098px" aria-label="Social link"></span>
</footer>

</body>
</html>
```